Detail Shop Business card design

i need a business card design for my new detailing company called 'Brisk's Polish Works'. i want an all black and white design . simple, direct and to the point. i want the designer to choose a fitting font to match the logothe front should have logo, address, phone and email and the back side should have a slogan and text indicating that we offer services on anything including cars, trucks, motorcycles and RVs. slogan will read "we take pride in your ride"
maybe also very small on the back side the IG icon with Brisks_Polish_Works

phone 208.417.6352
address 3847 E Larkin Ave
Spokane WA 99214
email: BrisksPolish@mailvexo.com

Target Market(s)

all ages , auto enthusiasts

Industry/Entity Type

Automotive

Contact Information for Business Card

the front should have logo, address, phone and email and the back side should have a slogan and text indicating that we offer services on anything including cars, trucks, motorcycles and RVs. slogan will read "we take pride in your ride"

phone 208.417.6352
address 3847 E Larkin Ave
Spokane WA 99214

Colors
000000
ffffff

Requirements
Must have
• bold font and very simple design with good spacing
Nice to have
• anything creative from the designer indicating we service any types of vehicles
Should not have
• any colors ,

```html
<!DOCTYPE html>
<html lang="en">
<head>
<meta charset="utf-8">
<title>Brisk's Polish Works – Business Card</title>
<link rel="stylesheet" href="https://fonts.googleapis.com/css2?family=Roboto:wght@400;500;700&family=Saira+Extra+Condensed:wght@600&display=swap">
<style>
  :root {
    --page: #e4e2df;
    --card: #f4f4f3;
    --band: #4d4d4d;
    --ink: #111111;
    --ink-soft: #4a4a4a;
    --rule: #9a9a9a;
    --white: #ffffff;
    --art-dark: #1a1a1a;
    --art-light: #d8d8d8;
  }
  * { margin: 0; padding: 0; box-sizing: border-box; }
  html, body { width: 1200px; height: 960px; overflow: hidden; }
  body { background: var(--page); position: relative; font-family: "Roboto", Arial, sans-serif; color: var(--ink); }

  .card {
    position: absolute; width: 600px; height: 343px;
    background: var(--card); overflow: hidden;
    box-shadow: 0 3px 8px rgba(0,0,0,0.25);
  }
  .card--front { left: 314px; top: 113px; }
  .card--back { left: 311px; top: 472px; }

  /* Front */
  .brand-band { position: absolute; left: 0; top: 23px; width: 100%; height: 142px; background: var(--band); }
  .brand-name {
    position: absolute; left: 0; top: 23px; width: 100%; height: 142px;
    display: flex; align-items: center; justify-content: center; gap: 12px;
    font-family: "Roboto", Arial, sans-serif; font-weight: 700; font-size: 30px;
    color: var(--white); letter-spacing: 0.5px;
  }
  .brand-dot { width: 14px; height: 14px; border-radius: 50%; background: var(--white); }

  .owner {
    position: absolute; right: 349px; top: 226px; text-align: right; white-space: nowrap;
  }
  .owner__name { font-weight: 500; font-size: 21px; line-height: 24px; color: var(--ink); }
  .owner__title { font-weight: 500; font-size: 15px; line-height: 20px; color: var(--ink-soft); margin-bottom: 3px; }
  .owner__line { font-size: 15px; line-height: 19px; color: var(--ink-soft); }

  .divider { position: absolute; left: 278px; top: 229px; width: 1px; height: 80px; background: var(--rule); }

  .contacts { position: absolute; left: 301px; top: 229px; list-style: none; }
  .contacts li { display: flex; align-items: center; height: 19.5px; font-size: 14.5px; color: var(--ink-soft); white-space: nowrap; }
  .contacts svg { width: 12px; height: 12px; margin-right: 10px; fill: var(--ink); flex: none; }

  /* Back */
  .services { position: absolute; left: 0; top: 44px; width: 600px; height: 34px; overflow: visible; }
  .services text {
    font-family: "Saira Extra Condensed", "Arial Narrow", sans-serif; font-weight: 600;
    font-size: 21px; fill: var(--ink);
  }
  .hero-art {
    position: absolute; left: 19px; top: 110px; width: 552px; height: 192px;
    background: radial-gradient(ellipse at 50% 55%, var(--art-dark) 0%, #3a3a3a 55%, var(--art-light) 100%);
    border-radius: 90px 60px 20px 20px;
  }
  .ground { position: absolute; left: 0; top: 0; width: 600px; height: 343px; }
  .slogan {
    position: absolute; left: 0; top: 306px; width: 100%; text-align: center;
    font-weight: 700; font-size: 16px; color: var(--white); letter-spacing: 0.3px;
  }
</style>
</head>
<body>

<section class="card card--front" aria-label="Business card front">
  <div class="brand-band"></div>
  <div class="brand-name"><span class="brand-dot"></span>Brisk's Polish Works</div>

  <div class="owner">
    <p class="owner__name">DALE HARMON</p>
    <p class="owner__title">CEO/FOUNDER</p>
    <p class="owner__line">3847 E Larkin Ave</p>
    <p class="owner__line">Spokane WA 99214</p>
  </div>

  <div class="divider"></div>

  <ul class="contacts">
    <li><svg viewBox="0 0 24 24"><path d="M6.6 10.8a15.1 15.1 0 0 0 6.6 6.6l2.2-2.2c.3-.3.7-.4 1-.2 1.1.4 2.3.6 3.6.6.6 0 1 .4 1 1V20c0 .6-.4 1-1 1A17 17 0 0 1 3 4c0-.6.4-1 1-1h3.5c.6 0 1 .4 1 1 0 1.3.2 2.5.6 3.6.1.3 0 .7-.2 1z"/></svg>208.417.6352</li>
    <li><svg viewBox="0 0 24 24"><path d="M7 1h10a2 2 0 0 1 2 2v18a2 2 0 0 1-2 2H7a2 2 0 0 1-2-2V3a2 2 0 0 1 2-2zm0 3v14h10V4zm5 15.5a1.2 1.2 0 1 0 0 2.4 1.2 1.2 0 0 0 0-2.4z"/></svg>208 553 7190</li>
    <li><svg viewBox="0 0 24 24"><path d="M2 5h20v14H2zm2 2v.5l8 5 8-5V7l-8 5z"/></svg>BrisksPolish@mailvexo.com</li>
    <li><svg viewBox="0 0 24 24"><path d="M12 2a10 10 0 1 0 0 20 10 10 0 0 0 0-20zm-1 17.9A8 8 0 0 1 4.1 10L9 15v1a2 2 0 0 0 2 2zm6.9-2.5A2 2 0 0 0 16 16h-1v-3a1 1 0 0 0-1-1H8v-2h2a1 1 0 0 0 1-1V7h2a2 2 0 0 0 2-2v-.4a8 8 0 0 1 2.9 12.8z"/></svg>www.briskspolish.com</li>
  </ul>
</section>

<section class="card card--back" aria-label="Business card back">
  <svg class="services" viewBox="0 0 600 34">
    <text x="71" y="24" textLength="448" lengthAdjust="spacingAndGlyphs">we offer services on anything including cars, trucks, motorcycles &amp; RVs</text>
  </svg>
  <div class="hero-art" role="img" aria-label="Black and white illustration of a classic hot rod car in side view"></div>
  <svg class="ground" viewBox="0 0 600 343" aria-hidden="true">
    <path d="M0 343 L0 326 C110 300 210 292 300 292 C390 292 500 302 600 320 L600 343 Z" fill="#000"/>
  </svg>
  <p class="slogan">WE TAKE PRIDE IN YOUR RIDE</p>
</section>

</body>
</html>
```